New Business Card for our Indoor Golf Training Facility

We are looking for designs for a new business card for our indoor golf training facility. Attached is our logo, our logo with our slogan, and here is our elevator pitch (What makes us different from the others) not sure if all the info will fit on one card, maybe you can condense the elevator pitch? here is the info

Elevator Pitch
We work with serious golfers and those that want to be serious golfers…
to make you better, faster, at all phases of the game…
We use the same state-of-the-art technology as professional golfers…
which produces data sets that shows your improvement in real time.
Our facility is available 24/7 to our members, which allows you to improve on your time.

our website: www.birchpinlinks.com

Target Market(s)

Golfers

Font styles to use
Serif
Sans Serif

Colors
ec1f27
f59195
fbd4d5
919191
d3d3d3
1b1b1b

Requirements
Must have
• our logo or our logo with the slogan, elevator pitch (can be condensed or shortened)

```html
<!DOCTYPE html>
<html lang="en">
<head>
<meta charset="utf-8">
<title>Birch Pin Links – Business Card</title>
<link rel="stylesheet" href="https://fonts.googleapis.com/css2?family=Roboto:wght@400;500;700&display=swap">
<style>
  :root {
    --red: #ec1f27;
    --red-soft: #f59195;
    --red-pale: #fbd4d5;
    --grey: #919191;
    --grey-light: #d3d3d3;
    --ink: #1b1b1b;
    --text: #444444;
    --paper: #ffffff;
    --stage: #ecebea;
  }
  * { box-sizing: border-box; margin: 0; padding: 0; }
  html, body { width: 1200px; height: 911px; overflow: hidden; }
  body {
    background: var(--stage);
    font-family: "Roboto", Arial, sans-serif;
    position: relative;
  }
  .card {
    position: absolute;
    top: 301px;
    width: 540px;
    height: 309px;
    background: var(--paper);
    border-radius: 18px;
    overflow: hidden;
    box-shadow: 0 6px 18px rgba(0,0,0,0.14);
  }
  .card--front { left: 40px; }
  .card--back { left: 620px; }

  /* front */
  .brand-name {
    position: absolute;
    top: 70px; right: 36px;
    width: 210px;
    color: var(--red);
    font-weight: 700;
    font-size: 40px;
    line-height: 1.05;
    text-align: center;
  }
  .contact {
    position: absolute;
    left: 34px; bottom: 30px;
  }
  .contact__name {
    color: var(--red);
    font-weight: 500;
    font-size: 25px;
    line-height: 1.1;
  }
  .contact__role {
    color: var(--ink);
    font-weight: 700;
    font-size: 13px;
    margin-bottom: 12px;
  }
  .contact__address {
    color: var(--text);
    font-size: 12.5px;
    line-height: 1.4;
    margin-bottom: 10px;
  }
  .contact__line {
    display: flex; align-items: center; gap: 8px;
    color: var(--text); font-size: 12.5px; line-height: 1.55;
  }
  .contact__line svg { width: 11px; height: 11px; flex: none; }

  /* back */
  .pitch-band {
    position: absolute;
    left: 0; top: 0;
    width: 262px; height: 100%;
    background: var(--red);
    color: var(--paper);
    padding: 30px 18px 0;
    text-align: center;
  }
  .pitch-band__text {
    font-size: 11.4px;
    font-weight: 500;
    line-height: 1.5;
  }
  .social {
    display: flex; justify-content: center; gap: 4px;
    margin-top: 16px;
  }
  .social span {
    width: 16px; height: 16px; border-radius: 50%;
    background: var(--paper);
  }
  .lockup {
    position: absolute;
    left: 292px; top: 108px;
    width: 220px;
  }
  .lockup__name {
    color: var(--red);
    font-weight: 700;
    font-size: 30px;
    line-height: 1;
    white-space: nowrap;
  }
  .lockup__slogan {
    margin-top: 14px;
    color: var(--red);
    font-size: 13px;
    font-weight: 400;
    white-space: nowrap;
  }
</style>
</head>
<body>
  <section class="card card--front" aria-label="Card front">
    <p class="brand-name">Birch Pin Links</p>
    <div class="contact">
      <p class="contact__name">Daniel Marsh</p>
      <p class="contact__role">Director of Instruction</p>
      <p class="contact__address">1480 W. Alder Rd. Unit B4<br>Fairview, OH 45108</p>
      <p class="contact__line">
        <svg viewBox="0 0 12 12"><path fill="#ec1f27" d="M2.4 1c.4-.3.9-.2 1.1.2l1 1.8c.2.4.1.8-.2 1.1l-.7.6c.5 1.1 1.4 2 2.5 2.6l.6-.7c.3-.3.8-.4 1.1-.2l1.8 1c.4.2.5.8.2 1.1l-.8.9C7.6 10.4 1.6 4.4 2.6 2.6z"/></svg>
        555-404-0199
      </p>
      <p class="contact__line">
        <svg viewBox="0 0 12 12"><rect x="1" y="2.5" width="10" height="7" rx="1" fill="#ec1f27"/><path d="M1.5 3l4.5 3.5L10.5 3" stroke="#fff" stroke-width="1" fill="none"/></svg>
        info@birchpinlinks.com
      </p>
      <p class="contact__line">
        <svg viewBox="0 0 12 12"><circle cx="6" cy="6" r="5" fill="#ec1f27"/><path d="M1 6h10M6 1c-2 2.5-2 7.5 0 10M6 1c2 2.5 2 7.5 0 10" stroke="#fff" stroke-width=".8" fill="none"/></svg>
        www.birchpinlinks.com
      </p>
    </div>
  </section>

  <section class="card card--back" aria-label="Card back">
    <div class="pitch-band">
      <p class="pitch-band__text">
        We work with serious golfers and those that want to be serious golfers…
        to make you better, faster, at all phases of the game…
        We use the same state-of-the-art technology as professional golfers…
        which produces data sets that shows your improvement in real time.
        Our facility is available 24/7 to our members, which allows you to improve on your time.
      </p>
      <div class="social" aria-label="Social links"><span></span><span></span></div>
    </div>
    <div class="lockup">
      <p class="lockup__name">Birch Pin Links</p>
      <p class="lockup__slogan">Practice Smart. Play Sharp. Every Day.</p>
    </div>
  </section>
</body>
</html>
```